Tallow Reed Software

We are a software company selling endpoint visibility, access and security technology to enterprise-level IT departments.

Our technology helps organizations gain comprehensive visibility into and control over devices accessing their corporate network so they can quickly identify and address suspicious activity on the network that could lead to potential threats like data breaches.

This technology can cost organizations upwards of $1M - depending on the size of the organization. Our primary clients are Pinnacle 2,000 companies.

We want a professional, polished business card to represent our new brand.

Info fields to include on the card:
Name
Job Title
Office Phone #
Cell Phone #
Email address
Address: 4270 Vestridge Pond Blvd., Ste. 2600, Larkfield, WI 55812
Website address: www.tallowreedsoftware.example
Tagline: See every device. Secure the network.

Logo files and color specs document are attached. Would like color scheme to coordinate with the logo.

Also looking at stationary/envelope designs in conjunction with the business card designs. Received very few designs that included the stationary.

Software

```html
<!DOCTYPE html>
<html lang="en">
<head>
<meta charset="utf-8">
<title>Tallow Reed Software — Presentation Folder</title>
<link rel="stylesheet" href="https://fonts.googleapis.com/css2?family=Montserrat:wght@600&family=Open+Sans:wght@400;600&display=swap">
<style>
  :root {
    --backdrop: #cdcdcd;
    --paper: #ffffff;
    --fold-tone: #f2f2f2;
    --brand-rust: #a8391f;
    --brand-copper: #c7744a;
    --ink-grey: #6f6f6f;
  }
  * { box-sizing: border-box; margin: 0; padding: 0; }
  html, body {
    width: 1200px;
    height: 1000px;
    overflow: hidden;
    background: var(--backdrop);
  }
  .canvas {
    position: relative;
    width: 1200px;
    height: 1000px;
  }
  .folder {
    position: absolute;
    left: 160px;
    top: 215px;
    width: 880px;
    height: 570px;
    display: flex;
    box-shadow: 0 12px 30px rgba(0, 0, 0, 0.12);
  }
  .folder-panel {
    position: relative;
    width: 440px;
    height: 570px;
    background: var(--paper);
  }
  .folder-panel--back {
    background: linear-gradient(to right, var(--paper) 88%, var(--fold-tone) 100%);
  }
  .folder-panel--front {
    background: linear-gradient(to right, var(--fold-tone) 0%, var(--paper) 10%);
  }

  /* Front cover */
  .cover-wordmark {
    position: absolute;
    top: 120px;
    left: 0;
    width: 100%;
    display: flex;
    align-items: center;
    justify-content: center;
    gap: 10px;
  }
  .cover-wordmark__square {
    width: 16px;
    height: 16px;
    background: var(--brand-copper);
  }
  .cover-wordmark__name {
    font-family: "Montserrat", sans-serif;
    font-weight: 600;
    font-size: 18px;
    letter-spacing: 0.06em;
    color: var(--brand-rust);
    text-transform: uppercase;
  }

  .cover-signoff {
    position: absolute;
    right: 26px;
    bottom: 40px;
    display: flex;
    align-items: center;
    gap: 8px;
  }
  .cover-signoff__square {
    width: 12px;
    height: 12px;
    background: var(--brand-copper);
  }
  .cover-signoff__name {
    font-family: "Montserrat", sans-serif;
    font-weight: 600;
    font-size: 11px;
    letter-spacing: 0.08em;
    color: var(--brand-rust);
    text-transform: uppercase;
    line-height: 1;
  }
  .cover-signoff__tagline {
    font-family: "Open Sans", sans-serif;
    font-size: 7px;
    color: var(--ink-grey);
    margin-top: 3px;
  }

  /* Back cover contact block */
  .contact-block {
    position: absolute;
    left: 34px;
    bottom: 34px;
    display: flex;
    align-items: center;
    gap: 10px;
  }
  .contact-block__square {
    width: 14px;
    height: 14px;
    background: var(--brand-copper);
  }
  .contact-block__list {
    list-style: none;
    border-left: 1px solid var(--brand-rust);
    padding-left: 6px;
    font-family: "Open Sans", sans-serif;
    font-size: 6px;
    line-height: 1.45;
    color: var(--ink-grey);
  }
  .contact-block__label {
    color: var(--brand-rust);
    font-weight: 600;
  }
</style>
</head>
<body>
<main class="canvas">
  <section class="folder" aria-label="Tallow Reed Software presentation folder, flat spread">
    <article class="folder-panel folder-panel--back">
      <div class="contact-block">
        <span class="contact-block__square" aria-hidden="true"></span>
        <ul class="contact-block__list">
          <li><span class="contact-block__label">Office:</span> 555-123-4567</li>
          <li><span class="contact-block__label">Cell:</span> 555-123-4568</li>
          <li><span class="contact-block__label">Email:</span> contact@tallowreedsoftware.example</li>
          <li><span class="contact-block__label">Web:</span> www.tallowreedsoftware.example</li>
          <li><span class="contact-block__label">Address:</span> 4270 Vestridge Pond Blvd.,</li>
          <li>Ste. 2600, Larkfield, WI 55812</li>
        </ul>
      </div>
    </article>

    <article class="folder-panel folder-panel--front">
      <div class="cover-wordmark">
        <span class="cover-wordmark__square" aria-hidden="true"></span>
        <span class="cover-wordmark__name">Tallow Reed Software</span>
      </div>

      <div class="cover-signoff">
        <span class="cover-signoff__square" aria-hidden="true"></span>
        <div>
          <p class="cover-signoff__name">Tallow Reed Software</p>
          <p class="cover-signoff__tagline">See every device. Secure the network.</p>
        </div>
      </div>
    </article>
  </section>
</main>
</body>
</html>
```